BildeVOLD buisnesscard

Hey :) I need a modern buisnesscard for my company BildeVOLD
It most have:
Dagligleder og Fotograf: Henrik Audun Strandvik

Mob: +4791264085
Epost: post@bildevold.example
Adresse: Kvernbakken9, 6040 Bjørkevik

Facbook and instagram logo with text BildeVOLD

BildeVOLD logo

It Company

```html
<!DOCTYPE html>
<html lang="no">
<head>
<meta charset="utf-8">
<title>BildeVOLD – visittkort</title>
<link rel="stylesheet" href="https://fonts.googleapis.com/css2?family=Source+Sans+3:wght@400;600;700&display=swap">
<style>
  :root {
    --brand-blue: #2a7db5;
    --brand-pink: #c94785;
    --text-grey: #444a50;
    --rule-grey: #8a8f94;
    --card-white: #ffffff;
    --page-bg: #e9e9eb;
    --faint-pink: #f7e8ef;
  }
  * { margin: 0; padding: 0; box-sizing: border-box; }
  html, body { width: 1105px; height: 1200px; overflow: hidden; }
  body {
    background: var(--page-bg);
    font-family: "Source Sans 3", "Segoe UI", sans-serif;
    position: relative;
  }
  .card {
    position: absolute;
    left: 193px;
    width: 720px;
    height: 410px;
    overflow: hidden;
  }
  .card--front { top: 167px; background: var(--card-white); }
  .card--back { top: 623px; background: var(--brand-pink); }

  .front-tint {
    position: absolute;
    left: 0;
    top: 0;
    width: 400px;
    height: 398px;
    background: linear-gradient(135deg, var(--faint-pink), rgba(247,232,239,0) 70%);
  }
  .brand-name {
    position: absolute;
    right: 44px;
    top: 104px;
    font-size: 44px;
    font-weight: 700;
    color: var(--brand-blue);
    line-height: 1;
  }
  .holder-name {
    position: absolute;
    left: 44px;
    top: 205px;
    font-size: 26px;
    font-weight: 600;
    color: var(--brand-blue);
    line-height: 1.2;
  }
  .holder-title {
    position: absolute;
    left: 44px;
    top: 238px;
    font-size: 18px;
    color: var(--brand-pink);
  }
  .divider {
    position: absolute;
    left: 44px;
    top: 279px;
    width: 630px;
    height: 1px;
    background: var(--rule-grey);
  }
  .contact-list {
    position: absolute;
    left: 44px;
    top: 296px;
    list-style: none;
    font-size: 18px;
    color: var(--text-grey);
    line-height: 26px;
  }
  .contact-list li { display: flex; align-items: center; gap: 10px; }
  .contact-list svg { width: 16px; height: 16px; fill: var(--brand-blue); }
  .address {
    position: absolute;
    right: 46px;
    top: 296px;
    font-style: normal;
    text-align: right;
    font-size: 18px;
    color: var(--text-grey);
    line-height: 26px;
  }
  .band-pink {
    position: absolute;
    left: 0;
    bottom: 0;
    width: 380px;
    height: 12px;
    background: var(--brand-pink);
  }
  .band-web {
    position: absolute;
    right: 0;
    bottom: 0;
    width: 362px;
    height: 44px;
    background: var(--brand-blue);
    clip-path: polygon(44px 0, 100% 0, 100% 100%, 0 100%);
    color: var(--card-white);
    font-size: 17px;
    letter-spacing: 3px;
    display: flex;
    align-items: center;
    justify-content: flex-end;
    padding-right: 24px;
  }

  .back-name {
    position: absolute;
    left: 0;
    right: 0;
    top: 165px;
    text-align: center;
    font-size: 64px;
    font-weight: 700;
    color: var(--card-white);
    line-height: 1;
  }
  .social-row {
    position: absolute;
    left: 0;
    right: 0;
    top: 344px;
    display: flex;
    align-items: center;
    justify-content: center;
    gap: 12px;
    color: var(--card-white);
    font-size: 16px;
  }
  .social-row .line {
    width: 125px;
    height: 1px;
    background: linear-gradient(to right, rgba(255,255,255,0), rgba(255,255,255,0.9));
  }
  .social-row .line--right {
    background: linear-gradient(to left, rgba(255,255,255,0), rgba(255,255,255,0.9));
  }
  .social-row .dot {
    width: 14px; height: 14px;
    border: 2px solid var(--card-white);
    border-radius: 50%;
  }
</style>
</head>
<body>
  <section class="card card--front">
    <div class="front-tint" aria-hidden="true"></div>
    <div class="brand-name">BildeVOLD</div>
    <h1 class="holder-name">Henrik Audun Strandvik</h1>
    <p class="holder-title">Dagligleder og Fotograf</p>
    <div class="divider"></div>
    <ul class="contact-list">
      <li>
        <svg viewBox="0 0 16 16" aria-hidden="true"><path d="M4 0h8a1.5 1.5 0 0 1 1.5 1.5v13A1.5 1.5 0 0 1 12 16H4a1.5 1.5 0 0 1-1.5-1.5v-13A1.5 1.5 0 0 1 4 0zm0 2v10h8V2zm4 11a1 1 0 1 0 0 2 1 1 0 0 0 0-2z"/></svg>
        +4791264085
      </li>
      <li>
        <svg viewBox="0 0 16 16" aria-hidden="true"><path d="M1 3h14v10H1zm1.2 1 5.8 4.6L13.8 4zM2 5.2V12h12V5.2L8 10z"/></svg>
        post@bildevold.example
      </li>
    </ul>
    <address class="address">Kvernbakken9<br>6040 Bjørkevik</address>
    <div class="band-pink"></div>
    <div class="band-web">www.bildevold.example</div>
  </section>

  <section class="card card--back">
    <div class="back-name">BildeVOLD</div>
    <div class="social-row">
      <span class="line"></span>
      <span class="dot"></span>
      <span>BildeVOLD</span>
      <span class="line line--right"></span>
    </div>
  </section>
</body>
</html>
```